4th Generation Family Business Needs a New Card Design!

We are a family owned 4th Generation company. We are based in the Sydney, Australia area and we are desperately in need of a more modern and classy card. We are monumental masons who design, supply & erect lasting memorials throughout cemeteries in Sydney. Our customers are normally in a period of grieving. I have attached logo files that will need to be implemented on the card. Company was established 1935. Australian Owned and Operated. Card needs to be designed to PIXO.com specification.

Target Market(s)

Our target market is based upon people that a grieving for family members that have passed away. We also deal with alot of companies that own and operate cemeteries.

Industry/Entity Type

Business

Contact Information for Business Card

Simon Harcourt, Operations Manager, 0417293086, simon@harcourtmemorials.com.au
Lewis Harcourt, Director, 0417293086, simon@harcourtmemorials.com.au
Phone # 02 9561 3048
Website: www.harcourtmemorials.com.au
Address: Suite 17, 8 Palfrey Lane, West Carlow, Sydney NSW 2156

Font styles to use
Serif
Decorative
Script

Requirements
Must have
• Would like to see the logo nicely implemented with a modern design. Embossed lettering would be a nice additive.

```html
<!DOCTYPE html>
<html lang="en">
<head>
<meta charset="utf-8">
<title>Harcourt Memorials — Business Card</title>
<link rel="stylesheet" href="https://fonts.googleapis.com/css2?family=Cinzel:wght@400;600&family=Old+Standard+TT:wght@400&display=swap">
<style>
  :root {
    --backdrop: #e4e4e4;
    --card-black: #0b0b0c;
    --card-black-soft: #2a2a2c;
    --card-white: #f6f6f6;
    --gold: #e0b321;
    --ink: #1a1a1a;
    --ink-soft: #3a3a3a;
    --brand-light: #f2f2f2;
  }
  * { margin: 0; padding: 0; box-sizing: border-box; }
  html, body { width: 1200px; height: 576px; overflow: hidden; background: var(--backdrop); }
  .canvas { position: relative; width: 1200px; height: 576px; }

  .card { position: absolute; top: 138px; height: 294px; box-shadow: 0 2px 6px rgba(0,0,0,.25); overflow: hidden; }

  /* Front */
  .card-front {
    left: 81px; width: 485px;
    background: linear-gradient(100deg, var(--card-black) 0%, var(--card-black) 24%, var(--card-black-soft) 34%, var(--card-black) 48%, var(--card-black) 100%);
  }
  .card-front .gold-band { position: absolute; left: 0; right: 0; bottom: 0; height: 10px; background: var(--gold); }
  .front-brand {
    position: absolute; left: 0; right: 0; top: 150px;
    text-align: center; color: var(--brand-light);
    font-family: "Cinzel", serif; font-weight: 400; font-size: 26px; letter-spacing: 1px;
  }

  /* Back */
  .card-back { left: 602px; width: 482px; background: var(--card-white); }
  .card-back .black-strip { position: absolute; left: 0; top: 0; bottom: 0; width: 41px; background: var(--card-black); }
  .card-back .gold-line { position: absolute; left: 41px; top: 0; bottom: 0; width: 4px; background: var(--gold); }

  .holder { position: absolute; left: 62px; top: 26px; color: var(--ink); }
  .holder-name { font-family: "Cinzel", serif; font-weight: 600; font-size: 19px; letter-spacing: .5px; }
  .holder-title { font-family: "Old Standard TT", serif; font-size: 11px; margin-top: 2px; }

  .back-brand {
    position: absolute; right: 24px; top: 118px;
    color: var(--ink);
    font-family: "Cinzel", serif; font-weight: 400; font-size: 17px; letter-spacing: .5px;
  }

  .contacts { position: absolute; left: 62px; top: 188px; list-style: none; font-family: "Old Standard TT", serif; font-size: 12.5px; color: var(--ink); }
  .contacts li { display: flex; align-items: center; height: 17.8px; }
  .contacts svg { width: 10px; height: 10px; margin-right: 11px; fill: var(--gold); }
  .address { position: absolute; left: 62px; top: 261px; font-family: "Old Standard TT", serif; font-size: 12.5px; color: var(--ink-soft); }
</style>
</head>
<body>
<main class="canvas">
  <section class="card card-front" aria-label="Card front">
    <div class="front-brand">Harcourt Memorials</div>
    <div class="gold-band"></div>
  </section>

  <section class="card card-back" aria-label="Card back">
    <div class="black-strip"></div>
    <div class="gold-line"></div>

    <div class="holder">
      <div class="holder-name">Simon Harcourt</div>
      <div class="holder-title">Operations Manager</div>
    </div>

    <div class="back-brand">Harcourt Memorials</div>

    <ul class="contacts">
      <li><svg viewBox="0 0 10 10" aria-hidden="true"><path d="M2 0.5 L3.8 2.6 L2.9 3.6 Q4 5.8 6.4 7.1 L7.4 6.2 L9.5 8 L8.3 9.5 Q3.5 8.8 0.5 1.8 Z"/></svg>0417293086</li>
      <li><svg viewBox="0 0 10 10" aria-hidden="true"><path d="M0.5 3.5 Q5 0.5 9.5 3.5 L8.5 4.8 L7 4 L7 3 L3 3 L3 4 L1.5 4.8 Z M2 5.5 L8 5.5 L9 9 L1 9 Z"/></svg>02 9561 3048</li>
      <li><svg viewBox="0 0 10 10" aria-hidden="true"><path d="M0.5 2 L9.5 2 L5 5.5 Z M0.5 3 L5 6.6 L9.5 3 L9.5 8.5 L0.5 8.5 Z"/></svg>simon@harcourtmemorials.com.au</li>
      <li><svg viewBox="0 0 10 10" aria-hidden="true"><circle cx="5" cy="5" r="4.5"/></svg>www.harcourtmemorials.com.au</li>
    </ul>
    <div class="address">Suite 17, 8 Palfrey Lane, West Carlow, Sydney NSW 2156</div>
  </section>
</main>
</body>
</html>
```